RM Installations Web Site Design

Need a basic site to show clients a little about what we do. We are a custom audio video company in the high-end residential market. Need a few basic but professional pages to show past projects and products we sell. No e-commerce. Should include my new logo from MarkBazaar.

Industry/Entity Type

Residential

Number of Pages Required

2 page

Font styles to use
Serif
Sans Serif

Colors
f78f20

Requirements
Must have
• Company Logo, Send feedback page
Nice to have
• I have no ideas about design, but I do know what I like and dislike when I see it.

```html
<!DOCTYPE html>
<html lang="en">
<head>
<meta charset="utf-8">
<title>RM Installations</title>
<link href="https://fonts.googleapis.com/css2?family=Oswald:wght@400;500;600&family=Lato:wght@400;700&display=swap" rel="stylesheet">
<style>
:root{
  --orange:#f78f20;
  --ink:#1c1c1c;
  --charcoal:#2b2b2b;
  --grey-line:#d6d6d6;
  --grey-text:#555;
  --light-band:#f1f1f1;
  --white:#ffffff;
  --footer:#151515;
}
*{margin:0;padding:0;box-sizing:border-box}
html,body{width:1200px;height:2731px;overflow:hidden;background:var(--white)}
body{position:relative;font-family:"Lato",Arial,sans-serif;color:var(--ink)}
.abs{position:absolute}
.heading{position:absolute;font-family:"Oswald",Arial,sans-serif;font-weight:500;font-size:31px;line-height:1.2;letter-spacing:.3px;text-transform:uppercase;white-space:nowrap;color:var(--ink)}
.heading span{color:var(--orange)}
.heading.centered{left:0;width:1200px;text-align:center}
.heading.small{font-size:22px}
.heading.on-orange{color:var(--ink)}
.heading.on-orange span{color:var(--white)}
.heading.on-dark{color:var(--white)}
.divider{position:absolute;height:1px;background:var(--grey-line)}
.divider::after{content:"";position:absolute;left:50%;top:-7px;width:14px;height:14px;margin-left:-7px;transform:rotate(45deg);background:var(--charcoal);border:3px solid var(--white);box-shadow:0 0 0 1px var(--grey-line)}
.divider.left::after{left:28px}
.divider.orange-band{background:rgba(255,255,255,.55)}
.divider.orange-band::after{border-color:var(--orange);box-shadow:0 0 0 1px rgba(255,255,255,.7)}
.divider.dark-band{background:rgba(255,255,255,.35)}
.divider.dark-band::after{border-color:#333;background:var(--orange);box-shadow:0 0 0 1px rgba(255,255,255,.5)}
.btn{position:absolute;height:28px;padding:0 14px;background:var(--charcoal);color:var(--white);font-size:13px;line-height:28px;letter-spacing:.5px;text-transform:uppercase;border:1px solid #555;white-space:nowrap}

/* hero */
.hero{left:0;top:0;width:1200px;height:601px;background:linear-gradient(180deg,#e8861f 0%,#f2a23e 45%,#f3ece3 62%,#e9e4dd 100%)}
.hero-band{left:0;top:470px;width:1200px;height:131px;background:rgba(15,15,15,.82)}
.nav{left:131px;top:29px;width:938px;height:73px;background:rgba(25,25,25,.92);box-shadow:0 3px 8px rgba(0,0,0,.4)}
.logo-box{left:131px;top:29px;width:224px;height:73px;background:var(--white);display:flex;align-items:center;padding-left:18px;gap:10px}
.logo-box .mark{width:30px;height:30px;background:var(--orange)}
.logo-box .name{font-weight:700;font-size:17px;color:var(--ink);text-transform:uppercase;line-height:1.05}
.nav-links{left:390px;top:29px;height:73px;display:flex;align-items:center;gap:29px;font-size:14px;color:var(--white);text-transform:uppercase}
.nav-links .active{border-bottom:3px solid var(--orange);padding:24px 0 22px}
.hero-title{left:131px;top:488px;font-family:"Oswald",sans-serif;font-weight:500;font-size:30px;line-height:1.2;color:var(--white);white-space:nowrap}
.hero-title span{color:var(--orange)}
.hero-sub{left:131px;top:534px;font-size:14.5px;line-height:21px;color:#e8e8e8}
.hero-arrows{left:1028px;top:560px;color:#bbb;font-size:30px}

/* services */
.card{position:absolute;top:734px;width:216px;height:270px;border:1px solid #ddd;background:var(--white)}
.card .photo{position:absolute;left:14px;top:14px;width:186px;height:124px}
.card h3{position:absolute;left:16px;top:148px;font-size:13.5px;font-weight:700;color:#222;white-space:nowrap}
.card p{position:absolute;left:16px;top:175px;width:186px;font-size:12px;line-height:18px;color:var(--grey-text)}
.card .btn{left:16px;top:222px;height:27px;line-height:27px;font-size:12px}
.side-arrow{position:absolute;top:843px;width:31px;height:31px;background:#cfcfcf;color:var(--white);font-size:22px;line-height:31px;text-align:center}

/* about */
.about-band{left:0;top:1052px;width:1200px;height:399px;background:var(--orange)}
.about-text{left:131px;top:1175px;width:530px;font-size:12px;line-height:20.5px;color:#fff6ec}
.about-text p+p{margin-top:6px}
.video{left:741px;top:1178px;width:328px;height:183px}
.video-bar{left:741px;top:1334px;width:328px;height:27px;background:rgba(20,20,20,.75)}

/* team */
.member{position:absolute;top:1581px;width:220px;text-align:center}
.diamond{position:absolute;left:32px;top:0;width:156px;height:156px;transform:translateY(27px) rotate(45deg);border:6px solid var(--orange);background:var(--white);padding:6px;box-shadow:0 4px 8px rgba(0,0,0,.15)}
.diamond .inner{width:100%;height:100%}
.member .name{position:absolute;left:0;top:238px;width:220px;font-size:16px;color:#333;text-transform:uppercase}
.member.active .name{color:var(--orange)}
.member.active .name::after{content:"";display:block;width:98px;height:2px;background:var(--orange);margin:10px auto 0}
.member.active .diamond{border-color:#222;background:#2a2a2a}

/* products */
.products{left:0;top:1899px;width:1200px;height:222px;background:var(--light-band)}
.brands{left:131px;top:2028px;width:960px;display:flex;justify-content:space-between;align-items:center}
.brand{font-family:"Oswald",sans-serif;font-weight:500;font-size:29px;color:#6a6a6a;display:flex;align-items:center;gap:8px;white-space:nowrap}
.brand i{display:block;width:16px;height:16px;border-radius:50%;background:#6a6a6a}
.chev{position:absolute;top:2032px;color:#b5b5b5;font-size:34px}

/* feedback */
.feedback{left:0;top:2121px;width:1200px;height:470px;background:linear-gradient(135deg,#1e1f22 0%,#33302c 45%,#1a1a1c 100%)}
.fb-text{left:131px;top:2255px;width:610px;font-size:14px;line-height:23px;color:#e3e3e3}
.field{position:absolute;height:31px;background:var(--white);font-size:11.5px;color:#999;padding:9px 10px}
.submit{left:131px;top:2506px;width:111px;height:26px;background:var(--orange);color:var(--white);font-size:12px;font-weight:700;text-align:center;line-height:26px;text-transform:uppercase}
.share-text{left:796px;top:2255px;width:275px;font-size:12px;line-height:21px;color:#e3e3e3}
.social{position:absolute;left:796px;display:flex;align-items:center;gap:20px;font-size:14px;color:var(--white)}
.social .ring{width:47px;height:47px;border-radius:50%;border:2px solid #ddd;display:flex;align-items:center;justify-content:center}

/* footer */
.footer{left:0;top:2591px;width:1200px;height:104px;background:var(--footer)}
.footer-bar{left:0;top:2695px;width:1200px;height:36px;background:#0b0b0b;color:#ccc;font-size:12px;text-align:center;line-height:36px}
.foot-col{position:absolute;display:flex;gap:12px;color:#ddd;font-size:12.5px;line-height:23px}
.foot-contacts{left:516px;top:2617px;color:#ddd;font-size:12.5px;line-height:23px}
.foot-contacts div{display:flex;gap:14px;align-items:center}
.foot-logo{left:885px;top:2617px;display:flex;align-items:center;gap:10px}
.foot-logo .mark{width:40px;height:40px;background:#cfcfcf}
.foot-logo .name{font-weight:700;font-size:17px;color:var(--white);text-transform:uppercase;line-height:1.05}
</style>
</head>
<body>

<!-- HERO -->
<div class="abs hero" role="img" aria-label="Home cinema room with orange wall, wall-mounted television, tall speakers and red lounge chairs"></div>
<div class="abs hero-band"></div>
<svg class="abs" style="left:572px;top:232px" width="56" height="56" viewBox="0 0 56 56" aria-hidden="true"><circle cx="28" cy="28" r="25" fill="none" stroke="#fff" stroke-width="4"/><path d="M22 16 L40 28 L22 40Z" fill="#fff"/></svg>
<div class="abs nav"></div>
<div class="abs logo-box"><div class="mark"></div><div class="name">RM<br>Installations</div></div>
<nav class="abs nav-links">
  <span class="active">Home</span><span>Our Team</span><span>Products</span><span>Past Project</span><span>Service</span><span>Feedback</span><span>Contact Us</span>
</nav>
<h1 class="abs hero-title">Welcom to <span>RM Installations</span></h1>
<p class="abs hero-sub">We expert in Residential Cinemas Make your Home<br>Safe &amp; Secure With our largest audio video control system</p>
<div class="abs hero-arrows">&#8249; <span style="color:#fff">&#8250;</span></div>

<!-- SERVICES -->
<h2 class="heading centered" style="top:638px">Our <span>Services</span></h2>
<div class="divider" style="left:484px;top:703px;width:232px"></div>

<div class="side-arrow" style="left:53px">&#8592;</div>
<div class="side-arrow" style="left:1116px">&#8594;</div>

<div class="card" style="left:131px">
  <div class="photo" role="img" aria-label="Media room with large screen showing a football game" style="background:linear-gradient(160deg,#3a2e26,#7a6a55 55%,#2a221c)"></div>
  <h3>Media Rooms</h3>
  <p>Lor ipsumdolorsitac nsectetur adipiscing elit d.uis.</p>
  <span class="btn">View Details</span>
</div>
<div class="card" style="left:372px">
  <div class="photo" role="img" aria-label="Two designers consulting over a laptop" style="background:linear-gradient(160deg,#d8d4cc,#9a8f82 55%,#c6c0b6)"></div>
  <h3>Design and Consultations</h3>
  <p>Lor ipsumdolorsitac nsectetur adipiscing elit d.uis.</p>
  <span class="btn">View Details</span>
</div>
<div class="card" style="left:612px">
  <div class="photo" role="img" aria-label="Dark room with blue ceiling lighting and a wall screen" style="background:linear-gradient(180deg,#2a6fd6,#0e1a35 45%,#1a1410)"></div>
  <h3>Automated Lighting Control</h3>
  <p>Lor ipsumdolorsitac nsectetur adipiscing elit d.uis.</p>
  <span class="btn">View Details</span>
</div>
<div class="card" style="left:854px">
  <div class="photo" role="img" aria-label="Operator watching a wall of security camera monitors" style="background:linear-gradient(160deg,#8aa1b5,#3d5266 55%,#a6b4c0)"></div>
  <h3>Security Camera Systems</h3>
  <p>Lor ipsumdolorsitac nsectetur adipiscing elit d.uis.</p>
  <span class="btn">View Details</span>
</div>

<!-- ABOUT -->
<div class="abs about-band"></div>
<h2 class="heading small on-orange" style="left:131px;top:1094px">About <span>RM Installations</span></h2>
<div class="divider left orange-band" style="left:131px;top:1148px;width:530px"></div>
<div class="abs about-text">
  <p>Lorem ipsum dolor sit amet, consectetur adipiscing elit. Aenean et dignissim sem, interdum risus. Vestibulum consectetur nisi mollis diam pulvinar adipiscing. Vestibulum ut urna nec nibh adipiscing facilisis. Etiam auctor porta lacus ac luctus. Praesent ac libero fermentum, rhoncus magna a, dapibus mauris. Nam ut auctor justo. Sed ante odio, luctus quis nequ nec, adipiscing eleifend arcu. Integer nunc turpis, porttitor at lorem ut.</p>
  <p>Quisque hendrerit molestie commodo. Aliquam imperdiet varius tortor ut condiment Nulla ornare ultricies nunc et scelerisque. Class aptent taciti sociosqu ad litora torquent conubia nostra, per inceptos himenaeos. Mauris mattis ultrices diam nec luctus.</p>
</div>
<span class="btn" style="left:131px;top:1378px">Read More</span>

<h2 class="heading small on-orange" style="left:741px;top:1094px">Past <span>Project Videos</span></h2>
<div class="divider left orange-band" style="left:741px;top:1148px;width:328px"></div>
<div class="abs video" role="img" aria-label="Video still of a hand holding a phone controlling a living room system" style="background:linear-gradient(120deg,#e9e6ea,#b9b4bd 50%,#4b4650)"></div>
<div class="abs video-bar"></div>
<div class="abs" style="left:777px;top:1346px;width:170px;height:3px;background:#bbb"><div style="width:75%;height:3px;background:#5aa0e0"></div></div>
<span class="btn" style="left:741px;top:1378px">View More</span>

<!-- TEAM -->
<h2 class="heading centered" style="top:1489px">Our <span>Team</span></h2>
<div class="divider" style="left:484px;top:1554px;width:232px"></div>

<div class="member" style="left:129px">
  <div class="diamond"><div class="inner" role="img" aria-label="Black and white portrait of a team member in a suit" style="background:linear-gradient(180deg,#9a9a9a,#3d3d3d)"></div></div>
  <div class="name">Colin Ward</div>
</div>
<div class="member" style="left:369px">
  <div class="diamond"><div class="inner" role="img" aria-label="Black and white portrait of a team member in a bow tie" style="background:linear-gradient(180deg,#a5a5a5,#2f2f2f)"></div></div>
  <div class="name">Peter Lindholm</div>
</div>
<div class="member active" style="left:611px">
  <div class="diamond"><div class="inner" role="img" aria-label="Darkened portrait of a team member with social link overlay" style="background:linear-gradient(180deg,#3a3a3a,#1e1e1e)"></div></div>
  <svg class="abs" style="left:56px;top:71px" width="108" height="44" viewBox="0 0 108 44" aria-hidden="true">
    <line x1="6" y1="2" x2="102" y2="2" stroke="#fff" stroke-width="1"/>
    <rect x="14" y="13" width="15" height="15" fill="#fff"/><rect x="36" y="13" width="15" height="15" fill="#fff"/>
    <rect x="58" y="13" width="15" height="15" fill="#fff"/><rect x="80" y="13" width="15" height="15" fill="#fff"/>
    <line x1="6" y1="40" x2="102" y2="40" stroke="#fff" stroke-width="1"/>
  </svg>
  <div class="name">Owen Marsh</div>
</div>
<div class="member" style="left:851px">
  <div class="diamond"><div class="inner" role="img" aria-label="Color portrait of a smiling team member" style="background:linear-gradient(180deg,#eadfd4,#b48a5e)"></div></div>
  <div class="name">Clara Benson</div>
</div>

<!-- PRODUCTS -->
<div class="abs products"></div>
<h2 class="heading centered" style="top:1940px">Products <span>Brand With Us</span></h2>
<div class="divider" style="left:484px;top:2005px;width:232px"></div>
<div class="chev" style="left:64px">&#8249;</div>
<div class="chev" style="left:1114px">&#8250;</div>
<div class="abs brands">
  <span class="brand">VANTO</span>
  <span class="brand">Lumen Audio</span>
  <span class="brand">Stratis</span>
  <span class="brand"><i></i>KORVEL</span>
  <span class="brand"><i></i>Halden</span>
  <span class="brand">Mirova</span>
</div>

<!-- FEEDBACK -->
<div class="abs feedback" role="img" aria-label="Blurred background photo of a home control room"></div>
<h2 class="heading on-dark" style="left:131px;top:2161px">Feedback</h2>
<div class="divider left dark-band" style="left:131px;top:2227px;width:605px"></div>
<p class="abs fb-text">Lorem Ipsum is simply dummy text of the printing and typesetting industry. Lorem Ipsum has b industry's standard dummy text ever since the 1500s.</p>
<div class="field" style="left:131px;top:2318px;width:199px">Name</div>
<div class="field" style="left:334px;top:2318px;width:198px">Phone no</div>
<div class="field" style="left:537px;top:2318px;width:199px">Email Id</div>
<div class="field" style="left:131px;top:2358px;width:605px;height:138px">Your Message</div>
<div class="abs submit">Submit</div>

<h2 class="heading on-dark" style="left:796px;top:2161px">Share <span>With Us</span></h2>
<div class="divider left dark-band" style="left:796px;top:2227px;width:273px"></div>
<p class="abs share-text">Lorem Ipsum is simply dummy text of t printing and typesetting industry.</p>
<div class="social" style="top:2312px"><span class="ring"></span>Circlebook</div>
<div class="social" style="top:2377px"><span class="ring"></span>Chirper</div>
<div class="social" style="top:2438px"><span class="ring"></span>Workline</div>
<div class="social" style="top:2500px"><span class="ring"><svg width="20" height="14" viewBox="0 0 20 14" aria-hidden="true"><rect x="0" y="0" width="20" height="14" rx="1" fill="#fff"/><path d="M1 1 L10 8 L19 1" fill="none" stroke="#333" stroke-width="1.6"/></svg></span>Email</div>

<!-- FOOTER -->
<div class="abs footer"></div>
<div class="foot-col" style="left:131px;top:2617px">
  <svg width="12" height="16" viewBox="0 0 12 16" style="margin-top:4px" aria-hidden="true"><path d="M6 0C2.7 0 0 2.6 0 5.8 0 10 6 16 6 16s6-6 6-10.2C12 2.6 9.3 0 6 0z" fill="#fff"/><circle cx="6" cy="5.8" r="2.2" fill="#151515"/></svg>
  <div>Contrary to popular belief,<br>Lorem Ipsum is.<br>1234567</div>
</div>
<div class="abs foot-contacts">
  <div><svg width="14" height="14" viewBox="0 0 14 14" aria-hidden="true"><path d="M3 0 L5 3.5 L3.6 5 C4.5 7 7 9.5 9 10.4 L10.5 9 L14 11 L12.5 14 C6 13.5 0.5 8 0 1.5Z" fill="#fff"/></svg>Phone: 123 456 789</div>
  <div><svg width="14" height="14" viewBox="0 0 14 14" aria-hidden="true"><rect x="3" y="0" width="8" height="4" fill="#fff"/><rect x="0" y="5" width="14" height="6" fill="#fff"/><rect x="3" y="9" width="8" height="5" fill="#fff" stroke="#151515"/></svg>Fax: 123 456 789</div>
  <div><svg width="14" height="10" viewBox="0 0 14 10" aria-hidden="true"><rect width="14" height="10" fill="#fff"/><path d="M0.5 0.5 L7 6 L13.5 0.5" fill="none" stroke="#151515" stroke-width="1.3"/></svg>info@rminstall.example</div>
</div>
<div class="abs foot-logo"><div class="mark"></div><div class="name">RM<br>Installations</div></div>
<div class="abs footer-bar">Copyright © 2015 RM Installations. All Rights Reserved.</div>

</body>
</html>
```